Coastal Learner Bureau business cards

Australian company about to start offering its services. We recruit international students to come to study English, vocational education and postgraduate courses in Australia. We help them find the institution and select the right city they want to come to Australia. We are a young, online oriented and supportive agency. Our clients are between 18 and 35 years old, mainly University students, young professionals or people with work experience. We provide much more information that any other agency offer. We administrate a Facebook group with more than 11.000 members that daily ask questions about general information when coming to Australia, while they are here and even after they leave the country

Target Market(s)

International students from South America, Central America and Europe

Industry/Entity Type

Student

Contact Information for Business Card

Tomas Bilbrea
Managing Director
tomas@kelvarin.com.au
www.kelvoria.com.au
+61 491058264
Melbourne, Australia

Font styles to use
Serif
Sans Serif

Colors

Designer to choose colors to be used in the design.

Requirements
Must have
• Horizontal design
• Standard business card size and shape. If font uses green or yellow colours, they will have to match the ones from the logo
Nice to have
• UPDATE: Use the contents of the green image to design one of the card sides. Use our logo in the background of that side as watermark.
• Passport image, or immigration stamps. A picture of the Yarra River (from Melbourne) would be cool as well.
Should not have
• Non-standard business card size and shape
• Not black as the background colour of any sides as we are not a VIP agency or a hight class service. We are orientes to young people and they like colours, pictures, something attractive.
• Vertical design
• NO YELLOW or BLACK AS THE BACKGROUND COLOUR OF ANY SIDE OF THE BIZ CARD

```html
<!DOCTYPE html>
<html lang="en">
<head>
<meta charset="utf-8">
<title>Coastal Learner Bureau – Business Cards</title>
<link href="https://fonts.googleapis.com/css2?family=Roboto:wght@400;500;700&family=Roboto+Condensed:wght@500;700&display=swap" rel="stylesheet">
<style>
  :root {
    --stage: #2c2c2c;
    --paper: #f3f3f3;
    --green: #0f5c3e;
    --gold: #d9ad12;
    --ink: #454545;
    --white: #ffffff;
  }
  * { margin: 0; padding: 0; box-sizing: border-box; }
  html, body {
    width: 1200px; height: 960px; overflow: hidden;
    background: var(--stage);
  }
  .canvas { position: relative; width: 1200px; height: 960px; }
  .card {
    position: absolute; width: 600px; height: 343px; overflow: hidden;
  }
  .card--front { left: 314px; top: 113px; background: var(--paper); }
  .card--back { left: 311px; top: 472px; background: var(--green); }

  .brand-name {
    position: absolute;
    font-family: "Roboto", sans-serif; font-weight: 700;
    white-space: nowrap; letter-spacing: -0.3px;
  }
  .card--front .brand-name {
    right: 40px; top: 84px; font-size: 27px; color: var(--green);
  }
  .card--back .brand-name {
    left: 0; right: 0; top: 152px; text-align: center;
    font-size: 40px; color: var(--white);
  }

  .holder { position: absolute; left: 41px; top: 172px; }
  .holder__name {
    font-family: "Roboto Condensed", sans-serif; font-weight: 700;
    font-size: 22px; line-height: 26px; color: var(--green); letter-spacing: 0.2px;
  }
  .holder__role {
    font-family: "Roboto Condensed", sans-serif; font-weight: 500;
    font-size: 16.5px; line-height: 20px; color: var(--gold); letter-spacing: 0.3px;
  }
  .contacts { position: absolute; left: 41px; top: 229px; list-style: none; }
  .contacts li {
    display: flex; align-items: center; height: 19.5px;
    font-family: "Roboto", sans-serif; font-size: 14.5px; color: var(--ink);
  }
  .contacts li:last-child { margin-top: 2px; }
  .contacts svg { width: 13px; height: 13px; margin-right: 8px; fill: var(--green); flex: none; }

  .tagline {
    position: absolute; left: 64px; right: 64px; top: 299px;
    display: flex; align-items: center; gap: 4px;
    font-family: "Roboto", sans-serif; font-size: 14.5px; color: var(--white);
    white-space: nowrap;
  }
  .tagline::before, .tagline::after {
    content: ""; flex: 1; height: 1px;
  }
  .tagline::before { background: linear-gradient(to right, rgba(255,255,255,0), rgba(255,255,255,0.85)); }
  .tagline::after { background: linear-gradient(to left, rgba(255,255,255,0), rgba(255,255,255,0.85)); }
</style>
</head>
<body>
<main class="canvas">
  <section class="card card--front" aria-label="Business card front">
    <div class="brand-name">Coastal Learner Bureau</div>
    <div class="holder">
      <h1 class="holder__name">TOMAS BILBREA</h1>
      <p class="holder__role">MANAGING DIRECTOR</p>
    </div>
    <ul class="contacts">
      <li>
        <svg viewBox="0 0 24 24" aria-hidden="true"><path d="M6.6 10.8a15.1 15.1 0 0 0 6.6 6.6l2.2-2.2c.3-.3.7-.4 1-.2 1.1.4 2.3.6 3.6.6.6 0 1 .4 1 1V20c0 .6-.4 1-1 1A17 17 0 0 1 3 4c0-.6.4-1 1-1h3.5c.6 0 1 .4 1 1 0 1.3.2 2.5.6 3.6.1.3 0 .7-.2 1z"/></svg>
        +61 491058264
      </li>
      <li>
        <svg viewBox="0 0 24 24" aria-hidden="true"><path d="M2 5h20v14H2zm2 2v.5l8 5 8-5V7zm0 2.8V17h16V9.8l-8 5z"/></svg>
        tomas@kelvarin.com.au
      </li>
      <li>
        <svg viewBox="0 0 24 24" aria-hidden="true"><path d="M12 2a10 10 0 1 0 0 20 10 10 0 0 0 0-20zm-1 17.9A8 8 0 0 1 4.1 10.3L9 15v1a2 2 0 0 0 2 2zm6.9-2.5A2 2 0 0 0 16 16h-1v-3a1 1 0 0 0-1-1H8v-2h2a1 1 0 0 0 1-1V7h2a2 2 0 0 0 2-2v-.4a8 8 0 0 1 2.9 12.8z"/></svg>
        www.kelvoria.com.au
      </li>
      <li>
        <svg viewBox="0 0 24 24" aria-hidden="true"><path d="M12 1.5a7.5 7.5 0 0 0-7.5 7.5c0 5.6 7.5 13.5 7.5 13.5S19.5 14.6 19.5 9A7.5 7.5 0 0 0 12 1.5zm0 10.5a3 3 0 1 1 0-6 3 3 0 0 1 0 6z"/></svg>
        Melbourne, Australia
      </li>
    </ul>
  </section>

  <section class="card card--back" aria-label="Business card back">
    <div class="brand-name">Coastal Learner Bureau</div>
    <p class="tagline">Hacemos más por ti!</p>
  </section>
</main>
</body>
</html>
```